Quarrybend Marble & Tile Needs a Business Card

Attached you will find your logo, my photo and design guidelines for a new business card. The final design will need two separate files to create an embossed card. The cards will be printed by www.plinkprint.com (Instructions below)
Format is the Plink SQUARE card
Quarrybend Marble And Tile is a brick and mortar, retail stone and tile shop.
One the front:
Quarrybend Marble And Tile
Dorian Fesslock
Owner
24807 Hollis Verdant Blvd
Suite P & R
Charlotte, NC 28193
Cell: 704-583-7142
Web: www.QuarrybendMarbleAndTile.com
(Make each word of the domain a different or alternating color)
On the back;
Something that shows beautiful colorful tile
Follow the design guide closely please. For more information see this page that describes creating the spot gloss file: https://www.plinkprint.com/us/business-cards/design-guidelines-spot-gloss
The logo is what we would like to have raised spot glossed.
Format is the Plink SQUARE card. See attahced guidlines.

```html
<!DOCTYPE html>
<html lang="en">
<head>
<meta charset="utf-8">
<title>Quarrybend Marble &amp; Tile – Business Card</title>
<link rel="stylesheet" href="https://fonts.googleapis.com/css2?family=Cinzel:wght@500&family=Open+Sans:wght@400&display=swap">
<style>
  :root {
    --backdrop: #b7b7b7;
    --card-dark: #121212;
    --card-dark-line: #050505;
    --emboss-text: #3a3a3a;
    --card-light: #ffffff;
    --navy: #1f2d38;
    --gold: #c8841f;
    --gold-rule: #b27a2c;
    --tile-slate: #283944;
    --photo-tone: #c3b5a2;
    --ink: #1d2a33;
  }
  * { margin: 0; padding: 0; box-sizing: border-box; }
  html, body { width: 1200px; height: 995px; overflow: hidden; }
  body { background: var(--backdrop); position: relative; font-family: "Open Sans", sans-serif; }

  .card { position: absolute; top: 296px; width: 401px; height: 402px; overflow: hidden; }

  /* back side */
  .card-back { left: 192px; background: var(--card-dark); }
  .card-back .brand {
    position: absolute; left: 30px; top: 140px;
    display: flex; align-items: center; gap: 14px;
  }
  .card-back .brand-mark { width: 56px; height: 56px; background: #1c1c1c; }
  .card-back .brand-name {
    font-family: "Cinzel", serif; font-weight: 500; font-size: 21px; line-height: 1.2;
    letter-spacing: 3px; color: var(--emboss-text); text-transform: uppercase;
  }
  .card-back .base-rule { position: absolute; left: 0; right: 0; top: 368px; height: 2px; background: var(--card-dark-line); }

  /* front side */
  .card-front { left: 607px; background: var(--card-light); }
  .tile-band { position: absolute; left: 0; top: 0; }
  .portrait {
    position: absolute; left: 11px; top: 84px; width: 129px; height: 150px;
    border-radius: 8px; background: var(--photo-tone);
  }
  .brand-name-front {
    position: absolute; left: 152px; top: 98px; width: 228px;
    font-family: "Cinzel", serif; font-weight: 500; font-size: 20px; line-height: 1.25;
    letter-spacing: 3px; color: var(--navy); text-transform: uppercase; text-align: center;
  }
  .contact { position: absolute; left: 160px; top: 183px; width: 233px; color: var(--ink); }
  .contact .name {
    font-family: "Cinzel", serif; font-weight: 500; font-size: 18px; line-height: 1.2;
    color: var(--navy); letter-spacing: .3px;
  }
  .contact .role { font-size: 14px; line-height: 1.2; color: var(--gold); }
  .contact .divider { width: 27px; height: 1px; background: var(--ink); margin: 8px 0 6px 2px; }
  .contact .line { font-size: 13.5px; line-height: 21px; white-space: nowrap; }
  .contact .web { letter-spacing: -0.2px; }
  .contact .accent { color: var(--gold); }
  .base-rule-gold { position: absolute; left: 0; right: 0; top: 366px; height: 3px; background: var(--gold-rule); }
</style>
</head>
<body>

  <section class="card card-back" aria-label="Card back">
    <div class="brand">
      <div class="brand-mark"></div>
      <div class="brand-name">Quarrybend<br>Marble &amp; Tile</div>
    </div>
    <div class="base-rule"></div>
  </section>

  <section class="card card-front" aria-label="Card front">
    <svg class="tile-band" width="401" height="402" viewBox="0 0 401 402" role="img" aria-label="Colourful geometric tile pattern">
      <polygon points="0,0 170,0 0,334" fill="var(--tile-slate)"/>
    </svg>
    <div class="portrait" role="img" aria-label="Portrait photo of the owner"></div>

    <div class="brand-name-front">Quarrybend<br>Marble &amp; Tile</div>

    <div class="contact">
      <p class="name">DORIAN FESSLOCK</p>
      <p class="role">Owner</p>
      <div class="divider"></div>
      <p class="line">704-583-7142</p>
      <p class="line web">www.<span class="accent">QuarrybendMarbleAndTile</span>.com</p>
      <div class="divider"></div>
      <p class="line">24807 Hollis Verdant Blvd,</p>
      <p class="line">Suite P &amp; R Charlotte, NC 28193</p>
    </div>

    <div class="base-rule-gold"></div>
  </section>

</body>
</html>
```